New Template, new corporate image Kelvoran 2022

New template designs for google slides or PowerPoint. Match to new corporate image. The new website www.kelvoran-mx.example Needs to match our new version. Technology and Artificial Intelligence elements to reflect our type of work.
We are adding old version of template and will send elements for the new corporate images.
Please consider our website as the main corporate image.
Our templates are being used on customer presentations, webminars, internal work only.
We have our main name of company Kelvoran. Kelvoran has to be in all the templates.
Secondary logo or branded service is: Vastrelim.

Target Market(s)

Industrial users. Asset managers. Corporate visitors and customers.

Industry/Entity Type

Automotive. Chemical. Food and Beverage. Manufacturing

Other font styles liked:
• GE INSPIRA. RALEWAY

Colors
0054AA
0677BA
7BADD7
CADEEF
E8F1F8

Requirements
Must have
• Match to our elements on the new image. Use Brain Icons. Chips icons to connect equipments with software and control. Innovation.
Nice to have
• Unique images, machine images. Connecting machines and data elements. Template version for google slides. Image for industrial software for control equipment and saving money to manufacturers. Segments: Automotive, Chemical, Food and Beverages, Mining and pharmaceutical, Energy Management
Should not have
• old elements. not to much images of medical devices. Do not seems like a hospital.

```html
<!DOCTYPE html>
<html lang="en">
<head>
<meta charset="utf-8">
<title>Kelvoran — Slide Template 2022</title>
<link rel="stylesheet" href="https://fonts.googleapis.com/css2?family=Raleway:wght@400;500;600;700;800&family=Poppins:wght@300;400;500&display=swap">
<style>
:root{
  --page:#4a4a4a;
  --brand:#0054aa;
  --brand-mid:#0677ba;
  --brand-deep:#0a3f9e;
  --brand-navy:#0b3a96;
  --sky:#7badd7;
  --mist:#cadeef;
  --ice:#e8f1f8;
  --ink:#1f1f1f;
  --grey:#5a5a5a;
  --night:#0a1633;
  --white:#ffffff;
}
*{box-sizing:border-box;margin:0;padding:0}
html,body{width:1200px;height:3413px;overflow:hidden}
body{background:var(--page);position:relative;font-family:'Poppins',sans-serif;color:var(--ink)}
.slide{position:absolute;left:50px;width:1102px;height:620px;overflow:hidden}
.slide svg.layer{position:absolute;left:0;top:0}
.abs{position:absolute}
.brand{font-family:'Raleway',sans-serif;font-weight:600;font-size:19px;letter-spacing:.5px;color:var(--white);display:flex;align-items:center;gap:8px}
.brand::before{content:"";width:9px;height:9px;background:currentColor;display:block}
.brand.blue{color:var(--brand)}
.h-title{font-family:'Raleway',sans-serif;font-weight:700;text-transform:uppercase}

/* slide 1 */
.s-welcome{top:52px;background:var(--night)}
.s-welcome .title{left:27px;top:180px;font-size:42px;line-height:49px;color:var(--white)}
.s-welcome .lead{left:27px;top:286px;width:470px;font-size:11.5px;line-height:21px;color:var(--white);font-weight:300}
.socials{left:27px;top:364px;display:flex;gap:7px}
.socials span{width:22px;height:22px;border-radius:50%;background:var(--white);display:block}

/* slide 2 */
.s-agenda{top:715px;background:radial-gradient(ellipse at 60% 40%,#0e4fb4 0%,var(--brand-deep) 70%)}
.s-agenda .heading{left:170px;top:225px;width:410px;text-align:center;font-size:72px;color:var(--white);letter-spacing:-1px}
.agenda-label{font-family:'Raleway',sans-serif;font-weight:700;font-size:17px;color:var(--white);text-transform:uppercase;transform:translateY(-50%)}

/* slide 3 */
.s-services{top:1379px;background:var(--white)}
.s-services .heading{left:0;width:100%;top:30px;text-align:center;font-size:27px;font-weight:600;color:var(--ink)}
.blurb{left:196px;width:710px;text-align:center;font-size:9.6px;line-height:21px;color:var(--ink)}
.svc-label{font-size:12.5px;line-height:13px;color:var(--white);text-align:center;width:130px;transform:translate(-50%,-50%)}

/* slide 4 */
.s-industries{top:2042px;background:var(--white)}
.s-industries .heading{left:65px;top:28px;font-size:34px;color:#1c1c1c;font-weight:700}
.industry{left:68px;width:420px}
.industry h3{font-family:'Raleway',sans-serif;font-weight:700;font-size:25px;color:#1c1c1c;text-transform:uppercase;display:flex;align-items:center;gap:11px}
.industry h3 i{width:15px;height:15px;border-radius:50%;background:var(--brand);display:inline-flex;align-items:center;justify-content:center}
.industry p{margin-left:22px;margin-top:6px;font-size:11.3px;line-height:22px;color:var(--grey);font-weight:300}

/* slide 5 */
.s-thanks{top:2706px;background:radial-gradient(ellipse at 75% 45%,#1b3f86 0%,#0d2153 45%,var(--night) 85%)}
.s-thanks .title{left:87px;top:115px;font-size:37px;color:var(--white)}
.s-thanks .lead{left:87px;top:160px;width:385px;font-size:9.3px;line-height:20px;color:var(--white);text-align:justify;font-weight:300}
.contact{left:87px;font-family:'Raleway',sans-serif;font-size:16px;color:var(--white);display:flex;align-items:center;gap:12px;transform:translateY(-50%)}
.contact svg{width:17px;height:17px;flex:none}
</style>
</head>
<body>

<!-- Slide 1: Welcome -->
<section class="slide s-welcome">
  <div class="abs" role="img" aria-label="Glowing digital brain rising from a circuit chip with data lines" style="left:470px;top:0;width:632px;height:620px;background:radial-gradient(ellipse at 50% 30%,#1ab4e6 0%,#0a5c8c 18%,#07203c 45%,#03060d 80%)"></div>
  <svg class="layer" width="1102" height="620" viewBox="0 0 1102 620">
    <defs>
      <linearGradient id="welcomePanel" x1="0" y1="0" x2="1" y2="1">
        <stop offset="0" stop-color="#0a6fd0"/>
        <stop offset=".55" stop-color="#1360c6"/>
        <stop offset="1" stop-color="#0a3e9e"/>
      </linearGradient>
    </defs>
    <polygon points="0,0 477,0 579,306 479,620 0,620" fill="url(#welcomePanel)"/>
    <polyline points="477,0 579,306 479,620" fill="none" stroke="#ffffff" stroke-width="5"/>
  </svg>
  <div class="abs brand" style="left:29px;top:26px">Kelvoran</div>
  <h1 class="abs title h-title">Welcome to<br>Industrial Data Hub</h1>
  <p class="abs lead">We are specialists in automation, process control, information technologies, development and consulting for quality, efficiency and production. Our goal is to always provide the best solutions in conjunction with our technology partners Travenix.</p>
  <div class="abs socials"><span></span><span></span><span></span><span></span></div>
</section>

<!-- Slide 2: Agenda -->
<section class="slide s-agenda">
  <div class="abs brand" style="left:62px;top:33px">Kelvoran</div>
  <h2 class="abs heading h-title">Agenda</h2>
  <svg class="layer" width="1102" height="620" viewBox="0 0 1102 620">
    <defs>
      <g id="agendaMark">
        <path d="M-22,-22 H10 A14,14 0 0 1 24,-8 V6 A16,16 0 0 1 8,22 H-14 L-20,28 L-20,22 H-22 Z" fill="#ffffff"/>
        <circle cx="0" cy="0" r="11" fill="none" stroke="#0a3f9e" stroke-width="1.8"/>
        <polyline points="-3,-5 2,0 -3,5" fill="none" stroke="#0a3f9e" stroke-width="1.8" stroke-linecap="round" stroke-linejoin="round"/>
      </g>
    </defs>
    <path d="M412,65 C570,65 660,180 660,310 C660,440 570,555 412,555" fill="none" stroke="#ffffff" stroke-width="1.3"/>
    <use href="#agendaMark" x="528" y="86"/>
    <use href="#agendaMark" x="620" y="164"/>
    <use href="#agendaMark" x="654" y="257"/>
    <use href="#agendaMark" x="654" y="363"/>
    <use href="#agendaMark" x="620" y="450"/>
    <use href="#agendaMark" x="546" y="522"/>
  </svg>
  <div class="abs agenda-label" style="left:576px;top:88px">About us</div>
  <div class="abs agenda-label" style="left:668px;top:166px">Our services</div>
  <div class="abs agenda-label" style="left:702px;top:259px">Industries we serve</div>
  <div class="abs agenda-label" style="left:702px;top:365px">See what our customers say</div>
  <div class="abs agenda-label" style="left:668px;top:452px">Our partners</div>
  <div class="abs agenda-label" style="left:594px;top:524px">Contact us</div>
</section>

<!-- Slide 3: Our services -->
<section class="slide s-services">
  <svg class="layer" width="1102" height="620" viewBox="0 0 1102 620">
    <polygon points="0,14 32,46 0,78" fill="var(--brand)"/>
    <line x1="53" y1="310" x2="1050" y2="310" stroke="#9aa3b0" stroke-width="1.2"/>
    <!-- lower halves -->
    <path d="M65,310 A71,71 0 0 0 207,310 Z" fill="var(--brand-navy)"/>
    <path d="M399,310 A71,71 0 0 0 541,310 Z" fill="var(--brand-navy)"/>
    <path d="M730,310 A71,71 0 0 0 872,310 Z" fill="var(--brand-navy)"/>
    <!-- upper halves -->
    <path d="M232,310 A71,71 0 0 1 374,310 Z" fill="#1b64b5"/>
    <path d="M565,310 A71,71 0 0 1 707,310 Z" fill="#1b64b5"/>
    <path d="M896,310 A71,71 0 0 1 1038,310 Z" fill="#1b64b5"/>
    <g fill="none" stroke="var(--brand-navy)" stroke-width="2" stroke-linecap="round" stroke-linejoin="round">
      <!-- tech support: gear over open hand -->
      <circle cx="136" cy="255" r="9"/>
      <circle cx="136" cy="255" r="16" stroke-dasharray="6 4"/>
      <path d="M108,282 h14 l10,-6 h18 l14,-8 M108,290 h40 l20,-12"/>
      <!-- certificate -->
      <rect x="283" y="323" width="40" height="32" rx="2"/>
      <path d="M290,332 h16 M290,340 h12 M290,347 h10"/>
      <circle cx="316" cy="338" r="7"/>
      <path d="M312,344 v14 l4,-3 l4,3 v-14"/>
      <!-- tech courses: monitor with cap -->
      <rect x="443" y="237" width="56" height="40" rx="3"/>
      <path d="M471,277 v8 M458,289 h26"/>
      <path d="M456,255 l15,-7 l15,7 l-15,7 z M462,258 v7 q9,5 18,0 v-7"/>
      <!-- diagnostics: chart with magnifier and gear -->
      <circle cx="622" cy="338" r="13"/>
      <path d="M613,347 l-9,10"/>
      <path d="M614,341 l5,-5 l5,3 l6,-7"/>
      <circle cx="648" cy="350" r="9"/>
      <circle cx="648" cy="350" r="3"/>
      <rect x="636" y="321" width="14" height="10" rx="1"/>
      <!-- consultancy: speech bubbles -->
      <path d="M778,240 h28 a4,4 0 0 1 4,4 v14 a4,4 0 0 1 -4,4 h-18 l-8,7 v-7 h-2 a4,4 0 0 1 -4,-4 v-14 a4,4 0 0 1 4,-4 z"/>
      <path d="M796,266 h26 a4,4 0 0 1 4,4 v12 a4,4 0 0 1 -4,4 h-2 v6 l-7,-6 h-17 a4,4 0 0 1 -4,-4 v-12 a4,4 0 0 1 4,-4 z"/>
      <path d="M786,251 h16 M804,276 h14"/>
      <!-- customer attention: checklist with star -->
      <rect x="945" y="322" width="44" height="36" rx="3"/>
      <path d="M953,332 l3,3 l5,-6 M966,332 h15 M953,344 l3,3 l5,-6 M966,344 h15"/>
      <path d="M967,318 l2,-5 l2,5 l5,0 l-4,3 l2,5 l-5,-3 l-5,3 l2,-5 l-4,-3 z"/>
    </g>
  </svg>
  <h2 class="abs heading h-title">Our Services</h2>
  <p class="abs blurb" style="top:82px">Lorem ipsum dolor sit amet, consectetur adipiscing elit, sed do eiusmod tempor incididunt ut labore et dolore magna aliqua. Quis ipsum suspendisse ultrices gravida. Risus commodo viverra maecenas accumsan lacus vel facilisis.Sed ut perspiciatis unde omnis iste natus error sit voluptatem accusantium doloremque laudantium, totam rem aperiam.</p>
  <div class="abs svc-label" style="left:136px;top:336px">Tech Support</div>
  <div class="abs svc-label" style="left:303px;top:271px">Certification</div>
  <div class="abs svc-label" style="left:470px;top:336px">Tech Courses</div>
  <div class="abs svc-label" style="left:636px;top:271px">Diagnostics</div>
  <div class="abs svc-label" style="left:801px;top:336px">Consultory</div>
  <div class="abs svc-label" style="left:967px;top:276px">Customer<br>Attention</div>
  <p class="abs blurb" style="top:449px">Lorem ipsum dolor sit amet, consectetur adipiscing elit, sed do eiusmod tempor incididunt ut labore et dolore magna aliqua. Quis ipsum suspendisse ultrices gravida. Risus commodo viverra maecenas accumsan lacus vel facilisis.Sed ut perspiciatis unde omnis iste natus error sit voluptatem accusantium doloremque laudantium, totam rem aperiam.</p>
  <div class="abs brand blue" style="left:935px;top:553px">Kelvoran</div>
</section>

<!-- Slide 4: Industries -->
<section class="slide s-industries">
  <svg class="layer" width="1102" height="620" viewBox="0 0 1102 620">
    <defs>
      <linearGradient id="plantTone" x1="0" y1="0" x2="0" y2="1">
        <stop offset="0" stop-color="#0e2a66"/>
        <stop offset=".5" stop-color="#1a3f86"/>
        <stop offset="1" stop-color="#0a1a3e"/>
      </linearGradient>
    </defs>
    <polygon points="0,14 32,46 0,78" fill="var(--brand)"/>
    <polygon points="625,0 1102,0 1102,620 621,620 519,310" fill="url(#plantTone)" role="img" aria-label="Chemical refinery plant lit in blue at night"/>
    <polyline points="625,0 519,310 621,620" fill="none" stroke="var(--brand)" stroke-width="4"/>
    <polyline points="608,0 503,310 604,620" fill="none" stroke="var(--brand)" stroke-width="1.5"/>
  </svg>
  <div class="abs brand" style="left:957px;top:26px">Kelvoran</div>
  <h2 class="abs heading h-title">Industries we serve</h2>
  <div class="abs industry" style="top:99px">
    <h3><i><svg width="8" height="8" viewBox="0 0 8 8"><polyline points="2.5,1 5.5,4 2.5,7" fill="none" stroke="#fff" stroke-width="1.6"/></svg></i>Chemical industry</h3>
    <p>You need a large-scale partner with products that easily connect and grow with your needs. But that is not all. You need solutions that help you predict the future.</p>
  </div>
  <div class="abs industry" style="top:227px">
    <h3><i><svg width="8" height="8" viewBox="0 0 8 8"><polyline points="2.5,1 5.5,4 2.5,7" fill="none" stroke="#fff" stroke-width="1.6"/></svg></i>Automotive</h3>
    <p>Accelerate your competitiveness. Our solution gives you manufacturing intelligence, execution, awareness, and discrete automation control throughout your plant.</p>
  </div>
  <div class="abs industry" style="top:355px">
    <h3><i><svg width="8" height="8" viewBox="0 0 8 8"><polyline points="2.5,1 5.5,4 2.5,7" fill="none" stroke="#fff" stroke-width="1.6"/></svg></i>Food and bev</h3>
    <p>The manufacturing of food, beverages and consumer goods operates in complex and interconnected environments. There are the constant pressures on cost.</p>
  </div>
  <div class="abs industry" style="top:483px">
    <h3><i><svg width="8" height="8" viewBox="0 0 8 8"><polyline points="2.5,1 5.5,4 2.5,7" fill="none" stroke="#fff" stroke-width="1.6"/></svg></i>Mining and metals</h3>
    <p>Process variability and unexpected equipment failures can be hampering the optimization of production, recovery, and asset availability.</p>
  </div>
</section>

<!-- Slide 5: Thank you -->
<section class="slide s-thanks">
  <div class="abs" role="img" aria-label="Hand holding a tablet projecting a glowing cloud with upload and download arrows over a city" style="left:590px;top:60px;width:512px;height:560px;background:radial-gradient(ellipse at 45% 40%,rgba(150,170,255,.55) 0%,rgba(60,100,200,.35) 30%,rgba(13,33,83,0) 70%)"></div>
  <svg class="layer" width="1102" height="620" viewBox="0 0 1102 620">
    <line x1="552" y1="111" x2="552" y2="526" stroke="#c9d3e8" stroke-width="1"/>
  </svg>
  <h2 class="abs title h-title">Thank you</h2>
  <p class="abs lead">We are specialists in automation, process control, information technologies, development and consulting for quality, efficiency and production. Our goal is to always provide the best solutions in conjunction with our technology partners Travenix.</p>
  <div class="abs contact" style="top:283px">
    <svg viewBox="0 0 24 24"><path d="M6.6 10.8a15 15 0 0 0 6.6 6.6l2.2-2.2a1 1 0 0 1 1-.25 11.4 11.4 0 0 0 3.6.57 1 1 0 0 1 1 1V20a1 1 0 0 1-1 1A17 17 0 0 1 3 4a1 1 0 0 1 1-1h3.5a1 1 0 0 1 1 1c0 1.25.2 2.45.57 3.57a1 1 0 0 1-.25 1z" fill="#2f78d8"/></svg>+52 81 5550 2718</div>
  <div class="abs contact" style="top:323px">
    <svg viewBox="0 0 24 24"><g fill="none" stroke="#2f78d8" stroke-width="2"><circle cx="12" cy="12" r="9"/><path d="M3 12h18M12 3c3 3 3 15 0 18M12 3c-3 3-3 15 0 18"/></g></svg>https://kelvoran-mx.example/</div>
  <div class="abs contact" style="top:364px">
    <svg viewBox="0 0 24 24"><rect x="2" y="5" width="20" height="14" rx="1.5" fill="#2f78d8"/><polyline points="3,6 12,13 21,6" fill="none" stroke="#0d2153" stroke-width="1.6"/></svg>info@kelvoran-mx.example</div>
  <div class="abs contact" style="top:405px">
    <svg viewBox="0 0 24 24"><path d="M12 2a7 7 0 0 0-7 7c0 5 7 13 7 13s7-8 7-13a7 7 0 0 0-7-7zm0 9.5A2.5 2.5 0 1 1 12 6.5a2.5 2.5 0 0 1 0 5z" fill="#2f78d8"/></svg>Monterrey, NL Calle Aurelio</div>
  <div class="abs contact" style="top:446px;left:116px"># 218, Col. Valdoria</div>
</section>

</body>
</html>
```